Cruise Booking Website

Cruise search and booking website

This project is a redesign of a cruise booking website we did a few years ago.

The current website is located here: http://voyage.pylonworks.example/en/

It's not fully functional but gives you ad idea how miserable the old design was.

All the information about cruises, cruise lines, destinations, ports and shore excursions will be similar to http://www.sailquest.example/
Actual search pages (form, results, single result, sailing and cabin selection, ship info, booking) will have EXACTLY the same info as sailquest.example

We like the style of http://harborfleetdesk.example, it's quite modern, good spacing, not overloaded with information. So you can use it as an example of what we like, not what we want as a final result for us. Please, don't copy it. The result should not be possible to resemble the harborfleetdesk.example, because our site has to be unique. This is important!
If you submit a design that clearly reminds another cruise site it will be rejected!

Also the mockup provided is just to give you the basic structure and show what information has to be present on the page. It doesn't mean the layout has to be the same as a mockup. The layout is up to the designer.

I've updated the mockup to be more generic so it doesn't confuse you:
https://files.boxvault.example/s/k7m2qp9wz4hx/Home%20page.png

When you're adding social sharing icons like plazanet/chirpline you have to use chinese ones instead:
https://files.boxvault.example/s/t3nr8vx5lc2e/chinese-social-icons.png
Originals: http://minilk.example/qR7t

We'll start with home page first and after it's approved inner pages can be designed.

I know the cost of the project doesn't look high, but the task is straight forward and doesn't require to be very original, it's better to follow existing design and layout patterns that proved to work well.
That's why I encourage you to choose a template to build the design on top of one of https://themeparlor.example/ themes if it will save the design work, will be easier and faster for you. So it will be more like a customization than a new design from scratch.

Mockups, site map and logo files:
- https://files.boxvault.example/sh/h48dm2rs73fkpw/QvnbW2Xz8e

Website tree:
- https://sheets.papernest.example/document/d/7xPqR2mLw9sTk4VbN8cHj3YzA6eUf5GdKo1iMnBv/edit?usp=sharing
Updates

So far a lot of designs are just copying http://www.harborfleetdesk.example/ - we don't like it!

We like the style of harborfleetdesk.example, it's quite modern, good spacing, not overloaded with information. So you can use it as an example of what we like, not what we want as a final result for us. Please, don't copy it. The result should not be possible to resemble the harborfleetdesk.example, because our site has to be unique. This is important!

Target Market(s)

Chinese travellers

Industry/Entity Type

Build

Requirements
Must have
• * White, blue and red
* Large spacing, not too much information cramped into a small space like sailquest.example or the current website
* More "hidden" info in popups, tabs and so on, so not to many things are visible at the same time
* Compatible with kestrel scaffold styling (for easier coding):
- http://kestrelkit.codeshelf.example/scaffold/index.html
- http://skinmarket.example/
* Feel free to propose to build the design on top of one of https://themeparlor.example/ themes if it will save the design work, will be easier and faster for you

```html
<!DOCTYPE html>
<html lang="en">
<head>
<meta charset="utf-8">
<title>Bluewake Cruises – Home</title>
<link href="https://fonts.googleapis.com/css2?family=Open+Sans:wdth,wght@75..100,300..800&display=swap" rel="stylesheet">
<style>
:root{
  --blue:#2a6ea8;
  --blue-dark:#1f5a8e;
  --blue-deep:#1a4f80;
  --accent:#2a8ac0;
  --teal:#4fb3d0;
  --red:#e2375a;
  --pale:#dde9f3;
  --tabbar:#b9cfe2;
  --text:#222;
  --white:#fff;
}
*{box-sizing:border-box;margin:0;padding:0}
html,body{width:1123px;height:1200px;overflow:hidden}
body{position:relative;font-family:"Open Sans",Arial,sans-serif;color:var(--text);background:var(--white)}
.abs{position:absolute}
.topbar{left:0;top:0;width:1123px;height:25px;background:var(--pale);font-size:11px;color:#4a7fb0}
.topbar .links{position:absolute;right:168px;top:6px;white-space:nowrap}
.topbar .links span{margin-left:10px}
.brand{left:169px;top:46px;display:flex;align-items:center;gap:10px;color:#1b6fa8;font-weight:700;font-size:33px;letter-spacing:-.5px;white-space:nowrap}
.brand .dot{width:46px;height:46px;border-radius:50%;background:#1b6fa8}
.brand small{display:block;font-size:12px;font-weight:600;letter-spacing:1px;color:#1b4f7a}
.hotline{right:173px;top:48px;display:flex;align-items:center;gap:8px;color:var(--red);font-size:31px;font-weight:600;white-space:nowrap}
.share{display:flex;gap:3px}
.share i{display:block;width:20px;height:20px;border-radius:4px;background:#7eaed6}
.share.head{position:absolute;right:170px;top:91px}
.nav{left:0;top:124px;width:1123px;height:30px;background:var(--blue)}
.nav ul{list-style:none;position:absolute;left:160px;top:0;display:flex;height:30px}
.nav li{color:#fff;font-size:12.5px;line-height:30px;text-align:center;white-space:nowrap;border-right:1px solid rgba(255,255,255,.15)}
.nav li.active{background:var(--teal)}
.search{position:absolute;left:834px;top:0;width:99px;height:30px;background:#fff;font-size:11px;color:#999;font-style:italic;padding:8px 14px}
.search-btn{position:absolute;left:933px;top:0;width:31px;height:30px;background:var(--red)}
.hero-bg{left:0;top:154px;width:1123px;height:305px;background:linear-gradient(180deg,#4d8fc4,#2f6fa8 60%,#4a88b8)}
.hero{left:162px;top:154px;width:803px;height:305px;background:linear-gradient(180deg,#cfe3f2 0%,#9fc2dc 14%,#2f6fa0 26%,#1f5a86 100%)}
.finder{left:721px;top:169px;width:232px;height:34px;background:rgba(20,30,40,.8);border:1px solid rgba(255,255,255,.4);color:#fff;font-size:15px;padding:6px 17px;white-space:nowrap}
.finder svg{position:absolute;right:12px;top:9px}
.caption{left:162px;top:387px;width:458px;height:61px;background:rgba(20,25,30,.85);color:#fff;font-size:29px;font-weight:700;font-stretch:85%;letter-spacing:-.5px;line-height:40px;padding:10px 0 0 23px;white-space:nowrap;overflow:hidden}
.dots{left:903px;top:438px;display:flex;gap:4px}
.dots i{width:10px;height:10px;background:#fff}
.dots i.on{background:var(--teal)}
.tabbar{left:0;top:459px;width:1123px;height:48px;background:var(--tabbar)}
.tabs{left:160px;top:459px;display:flex;height:48px}
.tabs div{height:48px;line-height:52px;font-size:12px;text-align:center;border-right:1px solid #fff;color:#111;white-space:nowrap}
.tabs .current{background:#fff}
.photo{left:180px;top:549px;width:289px;height:184px;background:#e6e6e6;padding:4px}
.photo div{width:100%;height:100%;background:linear-gradient(180deg,#6fa8d8 0%,#a9cbe4 30%,#dcc49e 60%,#c9a47a 100%)}
.intro{left:484px;top:545px;width:230px}
.intro h2{font-size:25px;font-weight:400;color:var(--accent)}
.intro p{font-size:11px;line-height:16px;margin:6px 0 0 4px}
.perks{list-style:none;margin:16px 0 0 4px}
.perks li{font-size:12px;color:var(--accent);display:flex;align-items:center;gap:8px;height:24.3px;white-space:nowrap}
.newsletter{left:724px;top:459px;width:240px;height:332px;background:#e3ecf4;padding:32px 20px 0 27px}
.newsletter h3{font-size:17px;font-weight:400;color:var(--accent);white-space:nowrap}
.newsletter .ship{width:191px;height:94px;margin-top:7px;background:linear-gradient(180deg,#8fc0e6 0%,#cde2f2 55%,#2f6fa8 70%,#1f5a86 100%)}
.newsletter p{font-size:11.5px;line-height:16px;margin-top:10px;width:180px}
.field{width:191px;height:30px;background:#fff;border:1px solid #cfd9e2;font-size:12px;font-style:italic;color:#555;padding:6px 11px;margin-top:7px}
.field.first{margin-top:10px}
.subscribe{width:191px;height:30px;background:var(--red);color:#fff;font-size:15px;padding:4px 0 0 60px;margin-top:11px;position:relative}
.subscribe svg{position:absolute;right:10px;top:7px}
.partners{left:162px;top:791px;width:802px;height:78px;border-top:1px solid #e3e3e3;overflow:hidden}
.partners .label{position:absolute;left:0;top:0;width:109px;height:78px;border-right:1px solid #e3e3e3;padding:12px 0 0 13px;color:#555;line-height:15px;white-space:nowrap}
.label .l1{font-size:14px}.label .l2{font-size:20px;line-height:20px}
.arrows{position:absolute;left:44px;top:49px;display:flex;gap:2px}
.arrows i{width:24px;height:22px;background:#ccc;display:block}
.arrows i+i{background:#888}
.badge{position:absolute;top:16px;width:110px;height:45px;border:2px solid #ddd;background:#fff}
.badge span{position:absolute;left:22px;top:13px;width:62px;height:15px;border-radius:3px;background:#c9d6e3}
.footer{left:0;top:869px;width:1123px;height:297px;background:var(--blue-dark);color:#fff}
.footer h2{position:absolute;left:0;width:1123px;top:30px;text-align:center;font-size:26px;font-weight:400;white-space:nowrap}
.fline{position:absolute;left:162px;width:802px;height:1px;background:rgba(255,255,255,.12)}
.col{position:absolute;top:98px}
.col h4{font-size:14px;font-weight:600;margin-bottom:24px;white-space:nowrap}
.col ul{list-style:none;margin-left:4px}
.col li{font-size:11px;height:19.3px;display:flex;align-items:center;gap:6px;white-space:nowrap}
.col .share{margin-top:10px}
.finput{position:absolute;left:758px;width:192px;background:#255f94;border:1px solid #2c6aa1;font-size:10px;font-style:italic;color:#8fb3d4;padding:6px 9px}
.send{position:absolute;left:885px;top:264px;width:66px;height:22px;background:#4f87b8;font-size:12px;text-align:center;line-height:22px}
.copy{left:0;top:1166px;width:1123px;height:34px;background:var(--blue-deep);color:#fff;font-size:9.5px;text-align:center;line-height:34px;white-space:nowrap}
</style>
</head>
<body>
<header>
  <div class="abs topbar"><div class="links"><span>➜ Sign in</span><span>| &nbsp;sign up</span></div></div>
  <div class="abs brand"><span class="dot"></span><div>Bluewake Cruises<small>www.bluewake.example</small></div></div>
  <div class="abs hotline">
    <svg width="24" height="24" viewBox="0 0 24 24" aria-hidden="true"><path fill="#e2375a" d="M6.6 10.8a15 15 0 0 0 6.6 6.6l2.2-2.2a1 1 0 0 1 1-.3 11 11 0 0 0 3.6.6 1 1 0 0 1 1 1V20a1 1 0 0 1-1 1A17 17 0 0 1 3 4a1 1 0 0 1 1-1h3.5a1 1 0 0 1 1 1 11 11 0 0 0 .6 3.6 1 1 0 0 1-.3 1z"/></svg>
    4008 512 903
  </div>
  <div class="share head"><i></i><i></i><i></i><i></i><i></i><i></i></div>
</header>

<nav class="abs nav">
  <ul>
    <li class="active" style="width:69px">Home</li><li style="width:62px">Lines</li><li style="width:70px">Shores</li><li style="width:101px">Destinations</li><li style="width:58px">FAQ</li><li style="width:62px">News</li><li style="width:98px">Promotions</li><li style="width:77px">Booking</li><li style="width:77px">Blog</li>
  </ul>
  <div class="search">Search...</div>
  <div class="search-btn"><svg width="31" height="30" viewBox="0 0 31 30" aria-hidden="true"><circle cx="17" cy="13" r="6" fill="none" stroke="#fff" stroke-width="2"/><path d="M12.5 17.5 9 21" stroke="#fff" stroke-width="2.5"/></svg></div>
</nav>

<section>
  <div class="abs hero-bg" role="img" aria-label="Blurred cruise ships on open water"></div>
  <div class="abs hero" role="img" aria-label="Large cruise ship sailing past a glacier"></div>
  <div class="abs finder">Find Your Cruise
    <svg width="14" height="14" viewBox="0 0 14 14" aria-hidden="true"><circle cx="7" cy="7" r="6" fill="none" stroke="#fff"/><path d="M7 3.5v6M4.5 7 7 9.5 9.5 7" fill="none" stroke="#fff"/></svg>
  </div>
  <div class="abs caption">All Inclusive Vacation Packages</div>
  <div class="abs dots"><i></i><i class="on"></i><i></i><i></i></div>
</section>

<main>
  <div class="abs tabbar"></div>
  <div class="abs tabs">
    <div class="current" style="width:105px">Book with us</div>
    <div style="width:99px">Deals</div>
    <div style="width:98px">Pakages</div>
    <div style="width:99px">News</div>
    <div style="width:163px">First Time Cruiser?</div>
  </div>

  <div class="abs photo"><div role="img" aria-label="Couple relaxing on a sandy beach by the sea"></div></div>
  <div class="abs intro">
    <h2>Book with us</h2>
    <p>We are the most advanced cruise booking provider in China</p>
    <ul class="perks">
      <li><svg width="12" height="12" viewBox="0 0 12 12" aria-hidden="true"><circle cx="6" cy="6" r="5" fill="none" stroke="#e2375a" stroke-width="1.4"/><path d="M6 3.3v5.4M3.3 6h5.4" stroke="#e2375a" stroke-width="1.4"/></svg>Great prices</li>
      <li><svg width="12" height="12" viewBox="0 0 12 12" aria-hidden="true"><circle cx="6" cy="6" r="5" fill="none" stroke="#e2375a" stroke-width="1.4"/><path d="M6 3.3v5.4M3.3 6h5.4" stroke="#e2375a" stroke-width="1.4"/></svg>Fast booking processing</li>
      <li><svg width="12" height="12" viewBox="0 0 12 12" aria-hidden="true"><circle cx="6" cy="6" r="5" fill="none" stroke="#e2375a" stroke-width="1.4"/><path d="M6 3.3v5.4M3.3 6h5.4" stroke="#e2375a" stroke-width="1.4"/></svg>20 cruise lines</li>
      <li><svg width="12" height="12" viewBox="0 0 12 12" aria-hidden="true"><circle cx="6" cy="6" r="5" fill="none" stroke="#e2375a" stroke-width="1.4"/><path d="M6 3.3v5.4M3.3 6h5.4" stroke="#e2375a" stroke-width="1.4"/></svg>Destinations around the world</li>
    </ul>
  </div>

  <aside class="abs newsletter">
    <h3>Cruise Deals Newsletter</h3>
    <div class="ship" role="img" aria-label="White cruise ship at sea under blue sky"></div>
    <p>Subscribe an recive the beals cruise deals now!</p>
    <div class="field first">Name</div>
    <div class="field">Email</div>
    <div class="subscribe">Subscribe
      <svg width="16" height="16" viewBox="0 0 16 16" aria-hidden="true"><circle cx="8" cy="8" r="7" fill="none" stroke="#fff" stroke-width="1.3"/><path d="M4.5 8h6M8 5.3 10.7 8 8 10.7" fill="none" stroke="#fff" stroke-width="1.3"/></svg>
    </div>
  </aside>

  <div class="abs partners">
    <div class="label"><div class="l1">Our Reliable</div><div class="l2">Partners</div>
      <div class="arrows"><i></i><i></i></div>
    </div>
    <div class="badge" style="left:126px"><span></span></div>
    <div class="badge" style="left:252px"><span></span></div>
    <div class="badge" style="left:378px"><span></span></div>
    <div class="badge" style="left:504px"><span></span></div>
    <div class="badge" style="left:630px"><span></span></div>
    <div class="badge" style="left:756px"><span></span></div>
  </div>
</main>

<footer class="abs footer">
  <h2>We are the most advanced cruise booking provider in China</h2>
  <div class="fline" style="top:91px"></div>
  <div class="fline" style="top:124px"></div>
  <div class="col" style="left:176px"><h4>Useful pages</h4>
    <ul><li>About us</li><li>Contact us</li><li>Blog</li><li>FAQ</li><li>Terms of Service</li><li>Payment info</li><li>Reward points</li></ul></div>
  <div class="col" style="left:371px"><h4>Cruise info</h4>
    <ul><li>Cruise news</li><li>Visa</li><li>Hunnymoon cruises</li><li>First time on a cruise?</li></ul></div>
  <div class="col" style="left:571px"><h4>Contact Us Today</h4>
    <ul><li>Address, Place,</li><li>Postcode/zipcode</li><li>Country</li>
      <li><svg width="9" height="9" viewBox="0 0 24 24" aria-hidden="true"><path fill="#fff" d="M6.6 10.8a15 15 0 0 0 6.6 6.6l2.2-2.2a1 1 0 0 1 1-.3 11 11 0 0 0 3.6.6 1 1 0 0 1 1 1V20a1 1 0 0 1-1 1A17 17 0 0 1 3 4a1 1 0 0 1 1-1h3.5a1 1 0 0 1 1 1 11 11 0 0 0 .6 3.6 1 1 0 0 1-.3 1z"/></svg>4008 512 903</li>
      <li><svg width="10" height="8" viewBox="0 0 10 8" aria-hidden="true"><rect x=".5" y=".5" width="9" height="7" fill="none" stroke="#fff"/><path d="M.5.5 5 4.5 9.5.5" fill="none" stroke="#fff"/></svg>info@bluewake.example</li></ul>
    <div class="share" style="margin-left:3px;gap:6px"><i></i><i></i><i></i><i></i><i></i><i></i></div>
  </div>
  <div class="col" style="left:760px"><h4>Send us a message</h4></div>
  <div class="finput" style="top:135px;height:26px">Full Name</div>
  <div class="finput" style="top:164px;height:26px">Email Address</div>
  <div class="finput" style="top:194px;height:62px;padding-top:9px">Message</div>
  <div class="send">Send</div>
</footer>
<div class="abs copy">Copyright © 2013 bluewake. Use of this website constitutes acceptance of our User Agreement and Privacy Policy.</div>
</body>
</html>
```